Book cover for book about Climate Change

Looking for a clean, bold, and attractive cover for a mass-market paperback (5.5"x 8.5") about solving the climate change problem. Title is either "Where the Rivers Meet” or A Harbor Made of Glass” (your choice), subtitle is "A practical field guide to mending the weather — so that the young ones after us inherit steady seasons and open skies," author is Lorne Whitcombe. Thinking that it *might* feature an image of Earth (or a portion thereof) and its very thin layer of atmosphere -- but STRONGLY encourage other ideas too!

Requirements
Nice to have
• Keep it positive — NOT scary doom-and-gloom

```html
<!DOCTYPE html>
<html lang="en">
<head>
<meta charset="utf-8">
<title>Where the Rivers Meet — Lorne Whitcombe</title>
<link href="https://fonts.googleapis.com/css2?family=Nunito:wght@900&family=Roboto+Condensed:wght@700&family=Arimo:wght@700&display=swap" rel="stylesheet">
<style>
  :root {
    --forest-deep: #1f3a1c;
    --forest-mid: #3f6a2a;
    --forest-light: #8fb85a;
    --title-green: #7dc21e;
    --letter-top: #8cc823;
    --letter-bottom: #00a03c;
    --ink: #1a1a1a;
    --paper: #ffffff;
    --band-red: #d9221a;
  }
  html, body {
    margin: 0;
    padding: 0;
    overflow: hidden;
    background: #e9e9e9;
  }
  .cover {
    position: relative;
    width: 776px;
    height: 1200px;
    overflow: hidden;
    background: var(--paper);
  }
  .forest-scene {
    position: absolute;
    left: 0; top: 0;
    width: 776px; height: 837px;
    background:
      radial-gradient(ellipse at 78% 20%, rgba(190,220,140,0.75) 0%, rgba(120,170,70,0.35) 35%, transparent 65%),
      linear-gradient(90deg, var(--forest-deep) 0%, var(--forest-mid) 35%, #5e8a36 65%, var(--forest-light) 100%);
  }
  .title-art {
    position: absolute;
    left: 0; top: 0;
    width: 776px; height: 837px;
  }
  .title-line {
    font-family: "Nunito", "Arial Rounded MT Bold", sans-serif;
    font-weight: 900;
    fill: var(--title-green);
    stroke: var(--ink);
    stroke-width: 3;
    paint-order: stroke;
  }
  .subtitle-line {
    font-family: "Roboto Condensed", "Arial Narrow", sans-serif;
    font-weight: 700;
    font-size: 38px;
    fill: var(--paper);
    stroke: var(--ink);
    stroke-width: 3.5;
    paint-order: stroke;
    text-anchor: middle;
  }
  .photo-strip {
    position: absolute;
    left: 0; top: 837px;
    width: 776px; height: 186px;
    background: var(--paper);
  }
  .author-band {
    position: absolute;
    left: 0; top: 1023px;
    width: 776px; height: 177px;
    background: var(--band-red);
  }
  .author-name {
    font-family: "Arimo", Arial, sans-serif;
    font-weight: 700;
    font-size: 96px;
    fill: var(--paper);
  }
</style>
</head>
<body>
<main class="cover">
  <div class="forest-scene" role="img" aria-label="Sunlit green forest with tall tree trunks and a hand holding up a fresh leaf"></div>

  <svg class="title-art" viewBox="0 0 776 837" aria-label="Where the Rivers Meet — A practical field guide to mending the weather">
    <defs>
      <linearGradient id="letter-fill" x1="0" y1="0" x2="0" y2="1">
        <stop offset="0" stop-color="var(--letter-top)"/>
        <stop offset="1" stop-color="var(--letter-bottom)"/>
      </linearGradient>
    </defs>

    <text class="title-line" x="42" y="168" font-size="92">Where The</text>
    <text class="title-line" x="42" y="247" font-size="92">Rivers</text>

    <text class="title-line big-letter" x="118" y="703" font-size="620" textLength="560" lengthAdjust="spacingAndGlyphs" fill="url(#letter-fill)" style="fill:url(#letter-fill)" stroke-width="4">M</text>
    <text class="title-line" x="588" y="704" font-size="92">eet</text>

    <text class="subtitle-line" x="212" y="330">"A practical</text>
    <text class="subtitle-line" x="212" y="376">field guide</text>
    <text class="subtitle-line" x="212" y="421">to mending</text>
    <text class="subtitle-line" x="373" y="466">the weather — so that the young ones</text>
    <text class="subtitle-line" x="504" y="514">after us</text>
    <text class="subtitle-line" x="504" y="559">inherit steady seasons</text>
    <text class="subtitle-line" x="504" y="605">and open</text>
    <text class="subtitle-line" x="499" y="650">skies"</text>
  </svg>

  <svg class="photo-strip" viewBox="0 0 776 186">
    <defs>
      <linearGradient id="coast" x1="0" y1="0" x2="0" y2="1">
        <stop offset="0" stop-color="#6aa8d8"/>
        <stop offset="0.35" stop-color="#cfe2ef"/>
        <stop offset="0.5" stop-color="#b59268"/>
        <stop offset="1" stop-color="#6e5a36"/>
      </linearGradient>
      <linearGradient id="wind" x1="0" y1="0" x2="0" y2="1">
        <stop offset="0" stop-color="#3d7fc8"/>
        <stop offset="0.35" stop-color="#d9e6f1"/>
        <stop offset="0.45" stop-color="#7fa83e"/>
        <stop offset="1" stop-color="#4f8a22"/>
      </linearGradient>
      <linearGradient id="field" x1="0" y1="0" x2="0" y2="1">
        <stop offset="0" stop-color="#f2c22c"/>
        <stop offset="0.35" stop-color="#f6e27a"/>
        <stop offset="0.45" stop-color="#6fa52c"/>
        <stop offset="0.75" stop-color="#4a7d1e"/>
        <stop offset="1" stop-color="#5c4a36"/>
      </linearGradient>
      <linearGradient id="river" x1="0" y1="0" x2="0" y2="1">
        <stop offset="0" stop-color="#e8613e"/>
        <stop offset="0.3" stop-color="#f0a35a"/>
        <stop offset="0.55" stop-color="#8a6a7e"/>
        <stop offset="1" stop-color="#9a4a2a"/>
      </linearGradient>
    </defs>
    <g role="img" aria-label="Rocky coastline with a boardwalk under a blue sky">
      <path d="M0 8 H246 Q190 100 130 178 H0 Z" fill="url(#coast)"/>
    </g>
    <g role="img" aria-label="Green hills with wind turbines under a cloudy sky">
      <path d="M246 8 H356 Q378 100 398 178 H130 Q190 100 246 8 Z" fill="url(#wind)"/>
    </g>
    <g role="img" aria-label="Rows of green crops in a field at golden sunrise">
      <path d="M356 8 H608 Q585 100 550 178 H398 Q378 100 356 8 Z" fill="url(#field)"/>
    </g>
    <g role="img" aria-label="River winding past red cliffs at sunset">
      <path d="M608 8 H776 V178 H550 Q585 100 608 8 Z" fill="url(#river)"/>
    </g>
    <g fill="none" stroke="var(--paper)" stroke-width="5">
      <path d="M246 8 Q190 100 130 178"/>
      <path d="M356 8 Q378 100 398 178"/>
      <path d="M608 8 Q585 100 550 178"/>
    </g>
  </svg>

  <svg class="author-band" viewBox="0 0 776 177">
    <text class="author-name" x="60" y="148" textLength="660" lengthAdjust="spacingAndGlyphs">LORNE WHITCOMBE</text>
  </svg>
</main>
</body>
</html>
```